Website design for legal tech start up in Switzerland (B2B)

We are for a legal tech start up in Switzerland called KOVA. We have been running since August 2016. This will be our first live website.

We need a website designed and business card design for our start-up in Switzerland. We also need the Web design to be converted into HTML and CSS files.

Function of website:
• To inform potential customers of our services
• Form a key part of our digital marketing and sales footprint.
• Branding

Please find attached logo.
Updates

Project Deadline Extended Reason: Giving us time to review submissions and provide opportunity for more submissions. Added Thursday, February 16, 2017

Project Deadline Extended
Reason: Looking for more idea's not necessarily set on blue and grey colours only.

Target Market(s)

B2B tech powered legal services.

Industry/Entity Type

Legal

Contact Information for Business Card

Lean and slick design.

Coding

Coded - Design and coding required

Number of Pages Required

5+ page

Requirements
Must have
• VERY LEAN AND CLEAN DESIGN!
• We have received many great standard designs, but we are looking for something more out-of-the box: You can get inspiration from these designs: http://www.pixelvane.com/websites/clean/
• Thanks!!
• Easy content management system
• Well structured coding for additional development
• Responsive webpage for all types of devices
• SEO optimized
• Tabs (Home, services, team, careers, blog, contact us)
• Colour scheme complementary to logo
Nice to have
• Look and Design - Approachable, High-tech, Modern
• Easy to add chat bot capability in future
Should not have
• Too busy/ too much clutter
• Not take to long to load

```html
<!DOCTYPE html>
<html lang="en">
<head>
<meta charset="utf-8">
<title>KOVA – Legal Services</title>
<link href="https://fonts.googleapis.com/css2?family=Open+Sans:wght@400;600;700&display=swap" rel="stylesheet">
<style>
:root{
  --navy:#1f3868;
  --ink:#333333;
  --text:#555555;
  --muted:#8a8a8a;
  --line:#cfcfcf;
  --band:#f5f5f5;
  --white:#ffffff;
  --footer:#474747;
  --footer-bottom:#3d3d3d;
  --footer-text:#d8d8d8;
}
*{box-sizing:border-box;margin:0;padding:0}
html,body{width:1200px;height:2459px;overflow:hidden}
body{font-family:"Open Sans",Arial,sans-serif;color:var(--text);background:var(--white);position:relative}
a{color:inherit;text-decoration:none}
.container{position:absolute;left:131px;width:938px}

/* header */
.site-header{position:absolute;top:0;left:0;width:1200px;height:108px;background:var(--white)}
.brand{position:absolute;left:131px;top:28px;font-size:46px;font-weight:700;letter-spacing:3px;color:#3a3a3a;line-height:52px}
.main-nav{position:absolute;right:131px;top:44px;display:flex;gap:30px;font-size:12.5px;text-transform:uppercase;color:#666}
.main-nav .active{color:var(--navy);font-weight:600}

/* hero */
.hero{position:absolute;top:108px;left:0;width:1200px;height:505px;
  background:linear-gradient(180deg,#c9dcec 0%,#d9d2c4 35%,#b58c66 60%,#7d6b5e 80%,#3f5665 100%)}
.hero-arrow{position:absolute;top:340px;width:22px;height:38px;background:rgba(0,0,0,.45)}
.hero-arrow.prev{left:0}.hero-arrow.next{right:0}
.hero-arrow svg{display:block;margin:11px auto}

/* headings */
.section-title{position:absolute;left:0;width:1200px;text-align:center;font-size:25px;font-weight:700;color:var(--navy);text-transform:uppercase}
.btn{position:absolute;border:1px solid var(--line);background:var(--white);color:#555;font-size:12px;text-align:center}

/* welcome */
.welcome-text{top:730px;font-size:12.3px;line-height:22.5px;text-align:center;color:#666}
.welcome-btn{left:556px;top:828px;width:88px;height:37px;line-height:35px;font-size:12.5px}

/* services */
.services{position:absolute;top:944px;left:0;width:1200px;height:407px;background:var(--band)}
.service{position:absolute;width:214px;text-align:center}
.service svg{display:block;margin:0 auto}
.service h3{margin-top:14px;font-size:21px;font-weight:400;color:var(--navy);text-transform:uppercase;line-height:26px}
.service p{margin-top:4px;font-size:10.5px;line-height:16.5px;color:#777}
.service .btn{position:relative;display:block;margin:10px auto 0;width:82px;height:37px;line-height:35px;font-size:10px;text-transform:uppercase;color:#888}

/* blog */
.blog-title{position:absolute;left:131px;top:1428px;font-size:24px;font-weight:700;color:var(--navy)}
.carousel-arrows{position:absolute;left:1013px;top:1433px;display:flex;gap:8px}
.carousel-arrows span{width:23px;height:22px;border:1px solid #999;display:block}
.carousel-arrows svg{display:block;margin:5px auto}
.post{position:absolute;top:1478px;width:298px}
.post-image{width:298px;height:181px;position:relative}
.post h3{margin-top:14px;font-size:15.5px;font-weight:400;line-height:22px;color:var(--ink)}
.post p{margin-top:10px;font-size:10.8px;line-height:17.5px;color:#888;text-align:justify}
.post-meta{margin-top:13px;display:flex;gap:18px;font-size:10.5px;color:#777;align-items:center}
.post-meta span{display:flex;gap:5px;align-items:center}

/* team */
.team{position:absolute;top:1900px;left:0;width:1200px;height:286px;background:var(--band)}
.member{position:absolute;top:118px;width:440px;height:100px}
.member-photo{position:absolute;left:0;top:0;width:97px;height:97px}
.member-body{position:absolute;left:108px;top:0;width:332px}
.member h3{font-size:16px;font-weight:400;color:var(--ink);text-transform:uppercase;line-height:20px}
.member .role{font-size:11.5px;color:#444;margin-top:5px}
.member p{margin-top:10px;font-size:10.8px;line-height:17.5px;color:#888;text-align:justify}
.member p b{color:#333;font-weight:600}

/* footer */
.site-footer{position:absolute;top:2186px;left:0;width:1200px;height:210px;background:var(--footer);color:var(--footer-text)}
.footer-heading{position:absolute;top:40px;font-size:16px;font-weight:400;color:var(--white)}
.contact-list{position:absolute;left:131px;top:73px;list-style:none;font-size:10.8px;line-height:15px}
.contact-list li{display:flex;gap:10px;margin-bottom:8px}
.contact-list svg{flex:none;margin-top:2px}
.footer-map{position:absolute;left:333px;top:74px;width:185px;height:102px;background:linear-gradient(135deg,#e4e4e4,#cfcfcf)}
.link-list{position:absolute;top:73px;list-style:none;font-size:10.8px;line-height:22px}
.link-list li::before{content:"•";margin-right:6px;color:#aaa}
.social{position:absolute;left:974px;top:75px;display:grid;grid-template-columns:26px 26px;gap:8px 7px}
.social span{width:26px;height:26px;border-radius:50%;background:#6f6f6f;display:block}
.footer-bottom{position:absolute;top:2396px;left:0;width:1200px;height:63px;background:var(--footer-bottom);border-top:1px solid #555;text-align:center;font-size:10.8px;color:#cfcfcf;line-height:38px}
</style>
</head>
<body>

<header class="site-header">
  <div class="brand">KOVA</div>
  <nav class="main-nav">
    <a class="active">Home</a><a>Services</a><a>Team</a><a>Careers</a><a>Blog</a><a>Contact us</a>
  </nav>
</header>

<section class="hero" role="img" aria-label="Photo of a lakeside old town with church towers and colourful houses">
  <span class="hero-arrow prev"><svg width="8" height="14" viewBox="0 0 8 14"><path d="M7 1 1 7l6 6" stroke="#fff" fill="none" stroke-width="1.5"/></svg></span>
  <span class="hero-arrow next"><svg width="8" height="14" viewBox="0 0 8 14"><path d="m1 1 6 6-6 6" stroke="#fff" fill="none" stroke-width="1.5"/></svg></span>
</section>

<section class="welcome">
  <h2 class="section-title" style="top:686px">Welcome to KOVA</h2>
  <p class="container welcome-text">Donec facilisis volutpat lorem, at euismod velit dignissim ac. Class aptent taciti sociosqu ad litora torquent per conubia nostra, per inceptos himenaeos. Nulla consequat ipsum id mi placerat viverra. Sed tempor ex id dui sagittis, at luctus tortor finibus. Vestibulum ante ipsum primis in faucibus orci luctus et ultrices posuere cubilia Curae; Duis varius condimentum tellus, a faucibus lorem vestibulum eu. Duis sit amet tellus nisl. Maecenas nec metus sodales ante sollicitudin auctor in quis velit. Maecenas libero nisi, dignissim eget nibh a, mollis eleifend tellus. Fusce maximus porttitor libero vitae viverra.</p>
  <a class="btn welcome-btn">Read more</a>
</section>

<section class="services">
  <h2 class="section-title" style="top:72px">Our Services</h2>
  <div class="service" style="left:131px;top:146px">
    <svg width="44" height="40" viewBox="0 0 44 40" fill="#1f3868"><circle cx="22" cy="9" r="7"/><circle cx="9" cy="13" r="5.5"/><circle cx="35" cy="13" r="5.5"/><path d="M11 38c0-10 4-19 11-19s11 9 11 19z"/><path d="M1 34c0-8 3-14 8-14 2 0 3 1 4 2-2 4-3 8-3 12z"/><path d="M43 34c0-8-3-14-8-14-2 0-3 1-4 2 2 4 3 8 3 12z"/></svg>
    <h3>Family Law</h3>
    <p>Duis varius ate condimentum tellus, faucibus lorem vestibulum eu. Duis sit amet tellus nisl. Maecenas nec metus sodales.</p>
    <a class="btn">Read more</a>
  </div>
  <div class="service" style="left:372px;top:146px">
    <svg width="48" height="40" viewBox="0 0 48 40" fill="#1f3868"><path d="M17 6V3h14v3h-3V5h-8v1z"/><rect x="2" y="8" width="44" height="30" rx="3"/><rect x="2" y="19" width="44" height="2" fill="#f5f5f5"/><rect x="21" y="17" width="6" height="6" fill="#f5f5f5"/></svg>
    <h3>Business Law</h3>
    <p>Duis varius ate condimentum tellus, faucibus lorem vestibulum eu. Duis sit amet tellus nisl. Maecenas nec metus sodales.</p>
    <a class="btn">Read more</a>
  </div>
  <div class="service" style="left:614px;top:146px">
    <svg width="52" height="40" viewBox="0 0 52 40" fill="#1f3868"><path d="M10 16 15 5h22l5 11h4a4 4 0 0 1 4 4v12H2V20a4 4 0 0 1 4-4z"/><path d="M15 16 18 8h16l3 8z" fill="#f5f5f5"/><circle cx="12" cy="24" r="3.5" fill="#f5f5f5"/><circle cx="40" cy="24" r="3.5" fill="#f5f5f5"/><rect x="5" y="31" width="8" height="7" rx="1"/><rect x="39" y="31" width="8" height="7" rx="1"/></svg>
    <h3>Vehicle Law</h3>
    <p>Duis varius ate condimentum tellus, faucibus lorem vestibulum eu. Duis sit amet tellus nisl. Maecenas nec metus sodales.</p>
    <a class="btn">Read more</a>
  </div>
  <div class="service" style="left:857px;top:146px">
    <svg width="52" height="40" viewBox="0 0 52 40" fill="#1f3868"><rect x="1" y="4" width="50" height="32"/><rect x="6" y="9" width="40" height="22" fill="#f5f5f5"/><circle cx="26" cy="20" r="9"/><path d="M24 15h3v10h-3z" fill="#f5f5f5"/></svg>
    <h3>Debt Law</h3>
    <p>Duis varius ate condimentum tellus, faucibus lorem vestibulum eu. Duis sit amet tellus nisl. Maecenas nec metus sodales.</p>
    <a class="btn">Read more</a>
  </div>
</section>

<section class="blog">
  <h2 class="blog-title">BLOG</h2>
  <div class="carousel-arrows">
    <span><svg width="6" height="10" viewBox="0 0 6 10"><path d="M5 1 1 5l4 4" stroke="#666" fill="none"/></svg></span>
    <span><svg width="6" height="10" viewBox="0 0 6 10"><path d="m1 1 4 4-4 4" stroke="#666" fill="none"/></svg></span>
  </div>

  <article class="post" style="left:131px">
    <div class="post-image" role="img" aria-label="Photo of a classical courthouse facade with columns" style="background:linear-gradient(180deg,#8ea3bf,#6e747c 55%,#4b4f55)"></div>
    <h3>Donec scelerisque felis at ante rhoncus, non mattis nulla facilisis</h3>
    <p>Integer gravida risus risus, in imperdiet leo convallis sed. Aenean lobortis neque, vitae faucibus lorem. Nulla dignissim tempus nisi, sed lobortis velit faucibus at. Fusce vel rutrum erat. Vivamus blandit interdum egestas.</p>
    <div class="post-meta"><span>♥ (28)</span><span>👍︎ (21)</span><span>▦ 8 Feb, 2017</span></div>
  </article>

  <article class="post" style="left:451px">
    <div class="post-image" role="img" aria-label="Photo of a hand stamping a document beside a justice statue" style="background:linear-gradient(135deg,#2c3342,#d9d9d9 45%,#f1f1f1 70%,#8a6d4a)"></div>
    <h3>Donec scelerisque felis at ante rhoncus, non mattis nulla facilisis</h3>
    <p>Integer gravida risus risus, in imperdiet leo convallis sed. Aenean lobortis neque, vitae faucibus lorem. Nulla dignissim tempus nisi, sed lobortis velit faucibus at. Fusce vel rutrum erat. Vivamus blandit interdum egestas.</p>
    <div class="post-meta"><span>♥ (28)</span><span>👍︎ (21)</span><span>▦ 8 Feb, 2017</span></div>
  </article>

  <article class="post" style="left:771px">
    <div class="post-image" role="img" aria-label="Video thumbnail of a riverside old town at dusk" style="background:linear-gradient(180deg,#5a6f86,#9c7454 50%,#3f4a4f)">
      <svg width="40" height="40" viewBox="0 0 40 40" style="position:absolute;left:129px;top:70px"><circle cx="20" cy="20" r="20" fill="#fff"/><path d="M16 12v16l12-8z" fill="#222"/></svg>
    </div>
    <h3>Donec scelerisque felis at ante rhoncus, non mattis nulla facilisis</h3>
    <p>Integer gravida risus risus, in imperdiet leo convallis sed. Aenean lobortis neque, vitae faucibus lorem. Nulla dignissim tempus nisi, sed lobortis velit faucibus at. Fusce vel rutrum erat. Vivamus blandit interdum egestas.</p>
    <div class="post-meta"><span>♥ (28)</span><span>👍︎ (21)</span><span>▦ 8 Feb, 2017</span></div>
  </article>
</section>

<section class="team">
  <h2 class="section-title" style="top:60px">Our Team</h2>
  <div class="member" style="left:131px">
    <div class="member-photo" role="img" aria-label="Portrait photo of Mark Hale" style="background:linear-gradient(180deg,#9a9a9a,#4a4a4a)"></div>
    <div class="member-body">
      <h3>Mark Hale</h3>
      <div class="role">Duis sed congue nibh</div>
      <p>Aenean lobortis neque, vitae faucibus lorem. Nulla dignissim tempus nisi, sed lobortis velit faucibus at. Fusce vel rutrum erat. Vivamus blandit interdum egestas. <b>More</b></p>
    </div>
  </div>
  <div class="member" style="left:628px">
    <div class="member-photo" role="img" aria-label="Portrait photo of Elena" style="background:linear-gradient(180deg,#b8b2a8,#8d7460)"></div>
    <div class="member-body">
      <h3>Elena</h3>
      <div class="role">Duis sed congue nibh</div>
      <p>Aenean lobortis neque, vitae faucibus lorem. Nulla dignissim tempus nisi, sed lobortis velit faucibus at. Fusce vel rutrum erat. Vivamus blandit interdum egestas. <b>More</b></p>
    </div>
  </div>
</section>

<footer class="site-footer">
  <h4 class="footer-heading" style="left:133px">Contact info</h4>
  <ul class="contact-list">
    <li><svg width="8" height="11" viewBox="0 0 8 11"><path d="M4 0a4 4 0 0 1 4 4c0 3-4 7-4 7S0 7 0 4a4 4 0 0 1 4-4z" fill="#ccc"/><circle cx="4" cy="4" r="1.5" fill="#474747"/></svg><span>24 Building name, Street name<br>City - Zipcode</span></li>
    <li><svg width="8" height="11" viewBox="0 0 8 11"><rect x="1" y="0" width="6" height="11" rx="1" fill="#ccc"/></svg><span>555 210 4873</span></li>
    <li><svg width="8" height="11" viewBox="0 0 8 11"><rect x="0" y="2" width="8" height="8" rx="1" fill="#ccc"/><rect x="2" y="0" width="4" height="3" fill="#ccc"/></svg><span>555 390 1267</span></li>
    <li><svg width="9" height="11" viewBox="0 0 9 11"><rect x="0" y="2" width="9" height="7" fill="#ccc"/><path d="m0 2 4.5 4L9 2" stroke="#474747" fill="none"/></svg><span>info@kova.com</span></li>
  </ul>
  <div class="footer-map" role="img" aria-label="Street map showing the office location"></div>

  <h4 class="footer-heading" style="left:645px">Links</h4>
  <ul class="link-list" style="left:645px"><li>Home</li><li>Services</li><li>Team</li><li>Careers</li><li>Blog</li></ul>
  <ul class="link-list" style="left:742px"><li>Contact us</li><li>Terms and conditions</li><li>Privacy Policy</li><li>Sitemap</li></ul>

  <h4 class="footer-heading" style="left:974px">Social Media</h4>
  <div class="social" aria-label="Social media links"><span></span><span></span><span></span><span></span></div>
</footer>
<div class="footer-bottom">Copyright © 2017 Company name. All rights reserved.</div>

</body>
</html>
```